Poster & Banner for Outback tour company

Poster needed for tour company in the Australian outback. We will need it in an A2 format and if possible a larger banner format as Well please. It needs the Galah Tours logo but also the other logos (less obvious). It also needs to feature the WanderRate logo (uploaded).

The poster needs a list of the tours we offer as well as some of the pictures uploaded.

List of tours:

- Premium Tour of the Town and the Breakaways $99
- Coober Pedy Highlights Tour $85
- Sunset Breakaways Tour $60
- Underground Noodling Tour $50

Industry/Entity Type

Tour Company

Font styles to use
Serif

Colors

Designer to choose colors to be used in the design.

Requirements
Must have
• Galah Tours logo/List of tours/

```html
<!DOCTYPE html>
<html lang="en">
<head>
<meta charset="utf-8">
<title>Explore Coober Pedy with Galah Tours</title>
<link rel="stylesheet" href="https://fonts.googleapis.com/css2?family=Lato:wght@300;700;900&display=swap">
<style>
  :root {
    --navy: #244a6e;
    --orange: #f0961e;
    --ink: #1c1c1c;
    --brown: #4a2a12;
    --white: #ffffff;
    --sand: #f3e3c8;
  }
  * { box-sizing: border-box; margin: 0; padding: 0; }
  html, body { width: 848px; height: 1200px; overflow: hidden; background: var(--navy); }
  .poster {
    position: relative; width: 848px; height: 1200px; overflow: hidden;
    background: var(--navy); font-family: "Lato", sans-serif;
  }
  .hero { position: absolute; left: 0; top: 0; width: 848px; height: 600px; }
  .brand {
    position: absolute; left: 636px; top: 46px; width: 170px; height: 84px;
    background: var(--white); border-radius: 6px;
    display: flex; align-items: center; justify-content: center; gap: 7px;
  }
  .brand-mark { width: 14px; height: 14px; background: var(--orange); flex: none; }
  .brand-name { font-weight: 900; font-size: 17px; color: var(--brown); letter-spacing: 0.3px; white-space: nowrap; }
  .headline {
    position: absolute; left: 0; top: 170px; width: 848px; text-align: center;
    color: var(--white); line-height: 60px;
  }
  .headline .light { font-weight: 300; font-size: 51px; display: block; }
  .headline strong { font-weight: 900; }
  .headline .second { font-weight: 900; font-size: 54px; display: block; }
  .tour {
    position: absolute; top: 396px; width: 185px; height: 356px;
    background: var(--white); border-radius: 93px;
    box-shadow: 0 8px 18px rgba(0,0,0,0.25);
  }
  .tour-photo {
    position: absolute; left: 13px; top: 12px; width: 159px; height: 170px;
    border-radius: 80px 80px 24px 24px;
  }
  .tour-title {
    position: absolute; left: 0; top: 194px; width: 185px; text-align: center;
    font-weight: 900; font-size: 20px; line-height: 24.5px; color: var(--ink);
  }
  .tour-price {
    position: absolute; left: 54px; top: 302px; width: 77px; height: 77px;
    border-radius: 50%; background: var(--orange); color: var(--white);
    display: flex; align-items: center; justify-content: center;
    font-weight: 900; font-size: 36px;
  }
  .photo-strip { position: absolute; top: 825px; left: 0; width: 848px; height: 169px; }
  .strip-photo {
    position: absolute; top: 0; width: 144px; height: 169px;
    border: 2px solid var(--white);
  }
  .award { background: var(--sand); display: flex; align-items: center; justify-content: center; }
  .award-seal { width: 72px; height: 72px; border-radius: 50%; background: var(--orange); }
  .partners { position: absolute; left: 0; top: 1030px; width: 848px; height: 144px; }
  .partner-name {
    position: absolute; top: 78px; transform: translate(-50%, -50%);
    font-weight: 900; font-size: 19px; text-align: center; line-height: 22px; white-space: nowrap;
  }
  .divider { position: absolute; top: 29px; width: 2px; height: 90px; background: #222; }
</style>
</head>
<body>
<main class="poster">
  <svg class="hero" viewBox="0 0 848 600" role="img" aria-label="Photograph of the colourful Breakaways mesas under a wide blue outback sky">
    <defs>
      <linearGradient id="sky" x1="0" y1="0" x2="0" y2="1">
        <stop offset="0" stop-color="#0f3566"/>
        <stop offset="0.4" stop-color="#3f78b4"/>
        <stop offset="0.55" stop-color="#9cc0de"/>
        <stop offset="0.6" stop-color="#c9a27a"/>
        <stop offset="0.75" stop-color="#b8663a"/>
        <stop offset="1" stop-color="#7a3a1f"/>
      </linearGradient>
    </defs>
    <path d="M0 0 H848 V450 Q424 660 0 450 Z" fill="url(#sky)"/>
  </svg>

  <div class="brand">
    <span class="brand-mark"></span>
    <span class="brand-name">GALAH TOURS</span>
  </div>

  <h1 class="headline">
    <span class="light">Explore <strong>Coober Pedy</strong> with</span>
    <span class="second">Galah Tours</span>
  </h1>

  <section class="tours">
    <article class="tour" style="left:20px">
      <div class="tour-photo" role="img" aria-label="Underground church with painted icons" style="background:linear-gradient(180deg,#a47a55,#6b3e1f 60%,#8a2a1a)"></div>
      <h2 class="tour-title">Premium Tour<br>of the Town<br>and the<br>Breakaways</h2>
      <div class="tour-price">$99</div>
    </article>
    <article class="tour" style="left:227px">
      <div class="tour-photo" role="img" aria-label="Tour bus seen through a sandstone arch" style="background:linear-gradient(180deg,#6f9bd0,#a9c3e0 55%,#c98a5a 75%,#9a5a34)"></div>
      <h2 class="tour-title">Coober<br>Pedy<br>Highlights<br>Tour</h2>
      <div class="tour-price">$85</div>
    </article>
    <article class="tour" style="left:431px">
      <div class="tour-photo" role="img" aria-label="Mining truck sign silhouetted at sunset" style="background:linear-gradient(180deg,#13204a,#3a3f7a 45%,#e0793a 75%,#0a0a0a 82%)"></div>
      <h2 class="tour-title">Sunset<br>Breakaways<br>Tour</h2>
      <div class="tour-price">$60</div>
    </article>
    <article class="tour" style="left:636px">
      <div class="tour-photo" role="img" aria-label="Visitor exploring an underground mine tunnel" style="background:linear-gradient(90deg,#a7aca6,#7e857f 55%,#4a3526)"></div>
      <h2 class="tour-title">Underground<br>Noodling<br>Tour</h2>
      <div class="tour-price">$50</div>
    </article>
  </section>

  <section class="photo-strip">
    <div class="strip-photo" style="left:33px;background:linear-gradient(180deg,#3f86d8,#8fbce8 55%,#e0b870 68%,#a35a30)" role="img" aria-label="Breakaways mesa under blue sky"></div>
    <div class="strip-photo" style="left:192px;background:linear-gradient(180deg,#4f86c8,#c7d8e6 40%,#e8e8e8 55%,#b8925e 75%)" role="img" aria-label="Tour coaches parked by palm trees"></div>
    <div class="strip-photo" style="left:351px;background:linear-gradient(180deg,#8a6a4a,#d8c8a0 45%,#5a3a2a)" role="img" aria-label="Two champagne glasses on red gravel"></div>
    <div class="strip-photo" style="left:510px;background:linear-gradient(180deg,#9aa6b4,#c07a4a 35%,#e8e4de 70%,#c9955f)" role="img" aria-label="Tour truck in front of a dugout cliff"></div>
    <div class="strip-photo award" style="left:669px" role="img" aria-label="WanderRate travellers award badge">
      <span class="award-seal"></span>
    </div>
  </section>

  <svg style="position:absolute;left:0;top:1030px" width="848" height="170" viewBox="0 0 848 170" aria-hidden="true">
    <path d="M0 16 Q424 -6 848 16 V143 H0 Z" fill="#ffffff"/>
  </svg>

  <section class="partners">
    <span class="partner-name" style="left:141px;color:#b5471c">Redstone<br>Outback Resort</span>
    <span class="divider" style="left:226px"></span>
    <span class="partner-name" style="left:307px;color:#2a5aa0">Gumtree<br>Holiday Parks</span>
    <span class="divider" style="left:386px"></span>
    <span class="partner-name" style="left:474px;color:#e08a1e">Saltbush<br>Villages</span>
    <span class="divider" style="left:572px"></span>
    <span class="partner-name" style="left:690px;color:#c45a1a">Dugout<br>Motel</span>
  </section>
</main>
</body>
</html>
```